PostCard Design Project

I am making a mailing postcard
I am having the mailing printed using 4 color foil on certain parts.
I am looking for a design that maximizes the foil process where certain parts are done in foil to grab the customers attention (example: if there is a car on the postcard the headlights would be done in foil) .
I am targeting some industries, (auto, real estate, medical, beauty) I would like the post card to have examples of postcard ideas for 2 or 3 of these industries.
specs:
the postcard should be atleast 6.5x9 up to 8.5x11, I don't want to restrict the space for the creative as I don't want everything to look like a huge mess. both sides will be used.
the piece is a direct mail piece so it has to meet requirements of https://www.mailvantor.com/business/pdf/quick-reference-guide.pdf
text will be
"business with no limits, meet mailing with no addresses, gain new customers through "Open Porch Route Drop" reach new customers at their home without needing their address. "
I also want some current print specials I am running included.
-double your order FREE (order 500 business cards and get 1000)
-250 100lb gloss stock brochures 99.00
-business packages (cards, envelopes and letterhead) 299
-1000 flyers 140.40
-5000 postcards 179.99
A list of services
banners
booklets
brochures
business cards
calendars
catalogs
CD/DVD packages
envelopes
event tickets
flyers
hangtags
postcards
posters
presentation folders
rack cards
labels
table tents
window cling and decal
"order 24/7 orders@inkwillow.com" must be included
my logo is InkWillow will be supplied later
ive received some great designs. however Im looking for something a little more modern like some zorvel would put out. if the amount of words is too much please feel free to edit. also an idea i had for the list of services i offer is to have it transparent yet readable as the background of the postcard some small some big but covering the entire backgroud. you can then design on top of that with other thing. just an early morning thought
Reason: I have uploaded a sketch of my idea, please take time to look at it for an accurate depiction of what im looking for. feel free to add elements that make it pop off the page
Reason: We are getting close i will be providing feed back today

```html
<!DOCTYPE html>
<html lang="en">
<head>
<meta charset="utf-8">
<title>InkWillow Mailing Postcard</title>
<link rel="stylesheet" href="https://fonts.googleapis.com/css2?family=Open+Sans:wght@400;600;700;800&display=swap">
<style>
  :root {
    --brown: #4f200c;
    --brown-mid: #6b2f12;
    --orange-deep: #ec6f1b;
    --orange: #f29521;
    --amber: #f6b42c;
    --ink: #2a1408;
    --white: #ffffff;
    --stage: #ececec;
  }
  * { box-sizing: border-box; margin: 0; padding: 0; }
  html, body {
    width: 1200px; height: 900px; overflow: hidden;
    background: var(--stage);
    font-family: "Open Sans", Arial, sans-serif;
  }
  .sheet {
    width: 1200px; height: 900px;
    display: flex; flex-direction: column; align-items: center; justify-content: center;
    gap: 24px;
  }
  .postcard {
    position: relative;
    width: 640px; height: 424px;
    overflow: hidden;
    background: linear-gradient(160deg, var(--amber) 0%, var(--orange) 45%, var(--orange-deep) 100%);
    box-shadow: 0 6px 18px rgba(0,0,0,.25);
  }

  /* ---------- front ---------- */
  .front__headline-band {
    position: absolute; left: 0; top: 0; width: 100%; height: 104px;
    background: var(--brown);
    padding: 14px 22px 0 22px;
  }
  .front__headline {
    color: var(--white); font-weight: 800; font-size: 17px; line-height: 1.28;
    text-align: center;
  }
  .logo-panel {
    position: absolute; right: 0; top: 104px; width: 150px; height: 320px;
  }
  .logo-panel svg { position: absolute; inset: 0; }
  .logo-panel__text {
    position: absolute; right: 18px; top: 132px; width: 90px;
    color: var(--ink); font-weight: 800; font-size: 15px; line-height: 1.2; text-align: center;
  }
  .front__cards-art {
    position: absolute; left: 420px; top: 112px; width: 92px; height: 70px;
    background: linear-gradient(135deg, #7a1e16, #2c0d0a);
    transform: rotate(-8deg);
    box-shadow: 3px 3px 6px rgba(0,0,0,.35);
  }
  .front__collage-art {
    position: absolute; left: 26px; top: 122px; width: 262px; height: 250px;
    background: linear-gradient(150deg, #e53b4c 0%, #3f8fd8 40%, #f4f7fb 70%, #f5c21e 100%);
    border-radius: 4px;
    transform: rotate(-6deg);
    box-shadow: 4px 5px 10px rgba(0,0,0,.3);
  }
  .specials {
    position: absolute; left: 306px; top: 210px; width: 220px;
    list-style: none; color: var(--ink); font-weight: 700; font-size: 11.5px; line-height: 1.35;
  }
  .specials li, .services li { position: relative; padding-left: 16px; }
  .specials li::before, .services li::before {
    content: ""; position: absolute; left: 2px; top: 3px;
    width: 5px; height: 8px;
    border: solid currentColor; border-width: 0 2px 2px 0;
    transform: rotate(40deg);
  }
  .order-line {
    position: absolute; color: var(--white); font-weight: 800; font-size: 18px;
  }
  .front .order-line { left: 26px; bottom: 18px; }

  /* ---------- back ---------- */
  .back__footer-band {
    position: absolute; left: 0; bottom: 0; width: 100%; height: 62px;
    background: var(--brown);
  }
  .back .order-line { right: 60px; bottom: 18px; }
  .postage-box {
    position: absolute; right: 34px; top: 22px; width: 66px; height: 50px;
    background: var(--white); border: 1px solid var(--ink);
    display: flex; align-items: center; justify-content: center; text-align: center;
    font-size: 10px; line-height: 1.2; color: var(--ink);
  }
  .services__title {
    position: absolute; left: 42px; top: 96px; width: 400px; height: 30px;
    background: rgba(79,32,12,.72);
    color: #f3dcc4; font-size: 17px; font-weight: 400;
    display: flex; align-items: center; justify-content: center;
  }
  .services {
    position: absolute; left: 42px; top: 146px;
    display: flex; gap: 34px;
  }
  .services ul {
    list-style: none; color: var(--ink); font-weight: 700; font-size: 17px; line-height: 1.45;
  }
</style>
</head>
<body>
<main class="sheet">

  <section class="postcard front" aria-label="Postcard front">
    <div class="front__headline-band">
      <p class="front__headline">“ Business with no limits, meet mailing with no addresses,<br>Gain new customers through "Open Porch Route Drop"<br>Reach new customers at their home without needing their address. ”</p>
    </div>

    <div class="logo-panel">
      <svg viewBox="0 0 150 320" width="150" height="320" aria-hidden="true">
        <path d="M150 0 L110 0 C40 60 20 180 70 320 L150 320 Z" fill="var(--white)"/>
        <path d="M110 0 C40 60 20 180 70 320" fill="none" stroke="var(--brown-mid)" stroke-width="9"/>
      </svg>
      <p class="logo-panel__text">YOUR LOGO HERE</p>
    </div>

    <div class="front__cards-art" role="img" aria-label="Stack of printed business cards"></div>
    <div class="front__collage-art" role="img" aria-label="Fanned collage of printed flyers and brochures"></div>

    <ul class="specials">
      <li>Double your order FREE<br>(order 500 business cards and get 1000)</li>
      <li>250 100lb gloss stock brochures 99.00</li>
      <li>business packages<br>(cards, envelopes and letterhead) 299</li>
      <li>1000 flyers 140.40</li>
      <li>5000 postcards 179.99</li>
    </ul>

    <p class="order-line">order 24/7 orders@inkwillow.com</p>
  </section>

  <section class="postcard back" aria-label="Postcard back">
    <div class="postage-box">Postage<br>Stamp</div>
    <h2 class="services__title">Our Services Are</h2>
    <div class="services">
      <ul>
        <li>banners</li>
        <li>booklets</li>
        <li>brochures</li>
        <li>business cards</li>
        <li>calendars</li>
        <li>catalogs</li>
      </ul>
      <ul>
        <li>CD/DVD packages</li>
        <li>envelopes</li>
        <li>event tickets</li>
        <li>flyers</li>
        <li>hangtags</li>
        <li>postcards</li>
      </ul>
      <ul>
        <li>posters</li>
        <li>presentation folders</li>
        <li>rack cards</li>
        <li>labels</li>
        <li>table tents</li>
        <li>window cling and decal</li>
      </ul>
    </div>
    <div class="back__footer-band"></div>
    <p class="order-line">order 24/7 orders@inkwillow.com</p>
  </section>

</main>
</body>
</html>
```